Moravel Aesthetic Doctor

I require an elegant, luxurious looking business card for my aesthetic business. I am a doctor and that will set me aside from competitors. I am planning to provide home and spa based treatments to clients with high expectations. I have attached my logo.

```html
<!DOCTYPE html>
<html lang="en">
<head>
<meta charset="utf-8">
<title>Moravel Aesthetic Doctor – Business Card</title>
<link rel="stylesheet" href="https://fonts.googleapis.com/css2?family=Work+Sans:wght@300;400;500&display=swap">
<style>
  :root {
    --page-bg: #161616;
    --card-bg: #262626;
    --card-bg-light: #2f2f2f;
    --accent: #0ba4ea;
    --text: #f2f2f2;
    --text-soft: #d8d8d8;
  }
  * { box-sizing: border-box; margin: 0; padding: 0; }
  html, body {
    width: 1200px; height: 900px; overflow: hidden;
    background: var(--page-bg);
    font-family: "Work Sans", Arial, sans-serif;
    color: var(--text);
  }
  .sheet {
    position: relative; width: 1200px; height: 900px;
    display: flex; flex-direction: column; align-items: center; justify-content: center; gap: 34px;
  }
  .card {
    position: relative; width: 700px; height: 400px;
    background: linear-gradient(135deg, var(--card-bg) 0%, var(--card-bg) 55%, var(--card-bg-light) 100%);
    border-bottom: 5px solid var(--accent);
    box-shadow: 0 14px 30px rgba(0,0,0,.55);
  }

  /* Front */
  .card--front { display: flex; flex-direction: column; align-items: center; justify-content: center; }
  .brand { display: flex; align-items: center; gap: 18px; margin-bottom: 46px; }
  .brand__dot { width: 70px; height: 70px; border-radius: 50%; border: 3px solid var(--accent); }
  .brand__name {
    font-weight: 300; font-size: 34px; letter-spacing: 4px; text-transform: uppercase;
    color: var(--text-soft); line-height: 1.15;
  }
  .services { text-align: center; font-size: 17px; letter-spacing: 1.4px; line-height: 1.6; color: var(--text); }
  .services .sep { color: var(--accent); margin: 0 6px; }

  /* Back */
  .card--back { display: flex; flex-direction: column; }
  .details { flex: 1; display: flex; align-items: center; justify-content: center; gap: 38px; padding-top: 40px; }
  .person { text-align: right; }
  .person__name { color: var(--accent); font-weight: 500; font-size: 22px; margin-bottom: 6px; }
  .person__title { font-size: 18px; letter-spacing: 1.2px; line-height: 1.3; }
  .divider { width: 2px; height: 70px; background: var(--accent); }
  .contact { list-style: none; font-size: 18px; letter-spacing: 1.2px; line-height: 1.45; }
  .contact li { display: flex; align-items: center; gap: 10px; }
  .contact svg { width: 13px; height: 13px; flex: none; }
  .tagline {
    text-align: center; font-size: 18px; letter-spacing: 2.4px; text-transform: uppercase;
    padding-bottom: 34px;
  }
</style>
</head>
<body>
<main class="sheet">
  <section class="card card--front">
    <div class="brand">
      <span class="brand__dot"></span>
      <span class="brand__name">Moravel<br>Aesthetic Doctor</span>
    </div>
    <p class="services">
      Dermal injectables<span class="sep">|</span>Plasma facials<span class="sep">|</span>Microneedling<br>
      Skin boosters<span class="sep">|</span>Excessive sweating
    </p>
  </section>

  <section class="card card--back">
    <div class="details">
      <div class="person">
        <p class="person__name">Dr Elise Varden MRCPCH MD</p>
        <p class="person__title">Australasian Diploma<br>of Aesthetic Medicine</p>
      </div>
      <span class="divider"></span>
      <ul class="contact">
        <li>
          <svg viewBox="0 0 24 24" aria-hidden="true"><path fill="var(--accent)" d="M6.6 10.8a15 15 0 0 0 6.6 6.6l2.2-2.2c.3-.3.7-.4 1-.2 1.1.4 2.3.6 3.6.6.6 0 1 .4 1 1V20c0 .6-.4 1-1 1A17 17 0 0 1 3 4c0-.6.4-1 1-1h3.5c.6 0 1 .4 1 1 0 1.3.2 2.5.6 3.6.1.3 0 .7-.2 1z"/></svg>
          0800 555 019
        </li>
        <li>
          <svg viewBox="0 0 24 24" aria-hidden="true"><rect x="2" y="5" width="20" height="14" fill="none" stroke="var(--accent)" stroke-width="2"/><path d="M2 5l10 8 10-8" fill="none" stroke="var(--accent)" stroke-width="2"/></svg>
          elise@moravel.co.nz
        </li>
        <li>
          <svg viewBox="0 0 24 24" aria-hidden="true"><circle cx="12" cy="12" r="10" fill="none" stroke="var(--accent)" stroke-width="2"/><path d="M2 12h20M12 2c3 3 3 17 0 20M12 2c-3 3-3 17 0 20" fill="none" stroke="var(--accent)" stroke-width="2"/></svg>
          www.moravel.co.nz
        </li>
      </ul>
    </div>
    <p class="tagline">Home and spa based treatments</p>
  </section>
</main>
</body>
</html>
```